Stylish Business Cards Wanted

- DOUBLE SIDED Design Required -

High end, edgy cards for a corporate and personal stylist. Must include logo,
Name: Belinda Harwick
Title: Director and Stylist
telephone : +61 8 7142 5809
email: belinda@theloombriefing.example
website: theloombriefing.example
Tag: Corporate Workwear & Uniform Specialist | Personal Stylist
Would like nice icons for telephone, email, website

Target Market(s)

Businesses wanting stylish uniforms, people wanting stylish wardrobes

Industry/Entity Type

Corporate Workwear Stylist

Contact Information for Business Card

I would like black, white and gold foiling incorporated in the design - possibly a touch of the other colours on my branding guide attached Name: Belinda Harwick Title: Director and Stylist telephone : +61 8 7142 5809 email: belinda@theloombriefing.example website: theloombriefing.example Tag: Corporate Workwear & Uniform Specialist | Personal Stylist Would like nice icons for telephone, email, website

Font styles to use
Other font styles liked:
• Raleway

Colors

Designer to choose colors to be used in the design.

Requirements
Must have
• Gold foil accents

```html
<!DOCTYPE html>
<html lang="en">
<head>
<meta charset="utf-8">
<title>The Loom Briefing — Business Card</title>
<link rel="stylesheet" href="https://fonts.googleapis.com/css2?family=Montserrat:wght@500;600&family=Raleway:wght@400;500;600&display=swap">
<style>
  :root {
    --bg: #dcdcdc;
    --ink: #0b0b0b;
    --ink-soft: #161818;
    --paper: #ffffff;
    --gold: #e6b84a;
    --gold-line: #efd9a2;
    --text: #1a1a1a;
  }
  * { box-sizing: border-box; margin: 0; padding: 0; }
  html, body { width: 1200px; height: 900px; overflow: hidden; }
  body {
    background: var(--bg);
    font-family: "Raleway", sans-serif;
    position: relative;
  }
  .card {
    position: absolute;
    left: 250px;
    width: 700px;
    height: 400px;
    box-shadow: 0 6px 18px rgba(0,0,0,0.25);
    overflow: hidden;
  }

  /* Front */
  .card-front { top: 35px; background: var(--ink); }
  .front-texture {
    position: absolute; inset: 0 0 92px 0;
    background: linear-gradient(135deg, var(--ink) 0%, var(--ink-soft) 50%, var(--ink) 100%);
  }
  .front-brand {
    position: absolute; top: 70px; right: 60px;
    font-weight: 600; font-size: 24px; color: var(--gold);
    letter-spacing: 0.5px;
  }
  .tag-band {
    position: absolute; left: 0; right: 0; bottom: 16px; height: 62px;
    border-top: 3px solid var(--gold);
    border-bottom: 3px solid var(--gold);
    display: flex; align-items: center; justify-content: center; gap: 16px;
    font-family: "Montserrat", sans-serif; font-weight: 500;
    font-size: 19px; color: var(--gold); letter-spacing: 0.5px;
  }

  /* Back */
  .card-back { top: 465px; background: var(--paper); display: flex; }
  .back-brand-side {
    position: relative; width: 300px; height: 100%;
    border-right: 1px solid #e4e4e4;
    box-shadow: 4px 0 8px -6px rgba(0,0,0,0.25);
    display: flex; align-items: center; justify-content: center;
  }
  .back-brand {
    font-weight: 600; font-size: 30px; color: var(--ink);
    text-align: center; line-height: 1.2; margin-bottom: 40px;
  }
  .gold-band { position: absolute; left: 0; right: 0; bottom: 0; height: 34px; background: var(--gold); }

  .back-info-side { position: relative; flex: 1; padding: 70px 50px 0 60px; }
  .person-name { font-size: 30px; font-weight: 600; color: var(--text); }
  .person-title { font-size: 17px; color: var(--gold); margin-top: 2px; }
  .name-rule { position: absolute; top: 98px; left: 280px; right: 40px; height: 1px; background: var(--gold-line); }

  .contact-list { list-style: none; margin-top: 70px; }
  .contact-item {
    display: flex; align-items: center; gap: 22px;
    padding: 10px 0 8px;
    border-bottom: 1px solid var(--gold-line);
    font-size: 19px; color: var(--text);
  }
  .contact-icon {
    width: 24px; height: 24px; border-radius: 50%;
    background: var(--ink); flex: none;
    display: flex; align-items: center; justify-content: center;
  }
  .ink-band { position: absolute; left: 0; right: 0; bottom: 0; height: 34px; background: var(--ink); }
</style>
</head>
<body>

<section class="card card-front">
  <div class="front-texture" role="img" aria-label="Tonal repeating brand-name pattern on black"></div>
  <div class="front-brand">The Loom Briefing</div>
  <div class="tag-band">
    <span>CORPORATE WORKWEAR</span><span>|</span>
    <span>UNIFORM SPECIALIST</span><span>|</span>
    <span>PERSONAL STYLIST</span>
  </div>
</section>

<section class="card card-back">
  <div class="back-brand-side">
    <div class="back-brand">The Loom<br>Briefing</div>
    <div class="gold-band"></div>
  </div>
  <div class="back-info-side">
    <h1 class="person-name">Belinda Harwick</h1>
    <p class="person-title">Director and Stylist</p>
    <div class="name-rule"></div>
    <ul class="contact-list">
      <li class="contact-item">
        <span class="contact-icon">
          <svg width="13" height="13" viewBox="0 0 24 24" fill="#e6b84a"><path d="M6.6 10.8a15 15 0 0 0 6.6 6.6l2.2-2.2c.3-.3.7-.4 1-.2 1.1.4 2.3.6 3.6.6.6 0 1 .4 1 1V20c0 .6-.4 1-1 1A17 17 0 0 1 3 4c0-.6.4-1 1-1h3.5c.6 0 1 .4 1 1 0 1.3.2 2.5.6 3.6.1.3 0 .7-.2 1z"/></svg>
        </span>
        +61 8 7142 5809
      </li>
      <li class="contact-item">
        <span class="contact-icon">
          <svg width="13" height="13" viewBox="0 0 24 24" fill="none" stroke="#e6b84a" stroke-width="2"><rect x="3" y="6" width="18" height="12"/><path d="M3 6l9 7 9-7"/></svg>
        </span>
        belinda@theloombriefing.example
      </li>
      <li class="contact-item">
        <span class="contact-icon">
          <svg width="13" height="13" viewBox="0 0 24 24" fill="none" stroke="#e6b84a" stroke-width="2"><circle cx="12" cy="12" r="9"/><path d="M3 12h18M12 3c3 3 3 15 0 18M12 3c-3 3-3 15 0 18"/></svg>
        </span>
        www.theloombriefing.example
      </li>
    </ul>
    <div class="ink-band"></div>
  </div>
</section>

</body>
</html>
```